Brovick Engineering Core Values Branding Package

Brovick Engineering has recently refined its company Core Values and is seeking a strong, cohesive branding package to visually bring these values to life. The new graphic assets will communicate our commitment to excellence in a way that resonates with our team, clients, and partners in a blue-collar, industrial environment.

We are looking for multiple visual assets with consistent design elements that can be applied across platforms. The tone should reflect strength, reliability, and professionalism while remaining approachable and aligned with our industry.

Core Values & Descriptions
Accountability
“We take ownership of our work and actions, ensuring reliability and trust in every solution we deliver.”

Teamwork
“We collaborate across departments and disciplines to provide the highest level of service and innovation for our clients.”

Integrity
“We operate with honesty, transparency, and ethical standards in all aspects of our business.”

Growth
“We are committed to continuous improvement—of our people, our processes, and our impact in the industry.”

Deliverables

1. Primary Core Values Graphic
A master visual representing all four values together.
Designed for use on posters, office signage, internal presentations.

2. Individual Value Graphics (x4)
One graphic per core value: Accountability, Teamwork, Integrity, Growth.
Cohesive style with slight visual variation to reflect each value’s unique meaning.

Target Market(s)

Employees of Brovick Engineering

Industry/Entity Type

Blue Collar

Font styles to use
Sans Serif

Colors
0054AA
0677BA
7BADD7
CADEEF
E8F1F8
00AB8E
00BBA5
67D7C9
C6EFE9
E9F9F6
EB3D1F
EC4F4E
F09395
F8D3D4
FCEDEE

Requirements
Must have
• Accountability, Teamwork, Integrity, Growth

```html
<!DOCTYPE html>
<html lang="en">
<head>
<meta charset="utf-8">
<title>Brovick Engineering – Core Values</title>
<link rel="stylesheet" href="https://fonts.googleapis.com/css2?family=Anton&family=Arimo:wght@700&display=swap">
<style>
  :root {
    --navy: #003063;
    --green: #3aaa35;
    --white: #ffffff;
    --ink: #111111;
  }
  * { margin: 0; padding: 0; box-sizing: border-box; }
  html, body { width: 731px; height: 1200px; overflow: hidden; background: var(--navy); }
  .poster { position: relative; width: 731px; height: 1200px; overflow: hidden; background: var(--navy); }
  .backdrop { position: absolute; inset: 0; width: 731px; height: 1200px; }
  .title {
    position: absolute; left: 0; top: 22px; width: 731px; text-align: center;
    font-family: "Anton", "Arial Narrow", sans-serif; font-size: 132px; line-height: 1;
    letter-spacing: -1px; transform: scaleX(0.98);
  }
  .title .core { color: var(--green); }
  .title .values { color: var(--navy); }
  .brand-name {
    position: absolute; left: 72px; top: 292px;
    font-family: "Anton", "Arial Narrow", sans-serif; font-size: 72px; line-height: 1;
    color: var(--navy); letter-spacing: 1px;
  }
  .value {
    position: absolute; width: 280px; text-align: center; color: var(--white);
  }
  .value-icon {
    display: block; margin: 0 auto 14px; width: 116px; height: 116px;
  }
  .value-name {
    font-family: "Anton", "Arial Narrow", sans-serif; font-size: 27px; line-height: 1.1;
    letter-spacing: 0.2px;
  }
  .value-text {
    margin-top: 6px;
    font-family: "Arimo", Arial, sans-serif; font-weight: 700; font-size: 12.5px; line-height: 1.35;
  }
  .accountability { left: 50px; top: 560px; }
  .teamwork { left: 392px; top: 560px; }
  .integrity { left: 50px; top: 854px; }
  .growth { left: 392px; top: 854px; }
  .website {
    position: absolute; left: 102px; top: 1152px; width: 160px; text-align: center;
    font-family: "Arimo", Arial, sans-serif; font-weight: 700; font-size: 16px; color: var(--white);
  }
</style>
</head>
<body>
<main class="poster">
  <svg class="backdrop" viewBox="0 0 731 1200" aria-hidden="true">
    <path class="swoosh-top" fill="#3aaa35" d="M0 268 C -4 440 130 548 300 530 C 470 512 630 388 731 250 L731 240 L572 185 Z"/>
    <path class="header-field" fill="#ffffff" d="M0 0 H731 V258 H592 L572 190 C 470 305 330 432 160 462 C 70 476 12 412 8 300 L0 300 Z"/>
    <path class="swoosh-bottom" fill="#3aaa35" d="M344 990 C 335 1100 390 1175 440 1200 L731 1200 L731 1085 C 650 1160 520 1210 430 1165 C 380 1135 350 1070 344 990 Z"/>
  </svg>

  <h1 class="title"><span class="core">CORE</span> <span class="values">VALUES</span></h1>
  <div class="brand-name">BROVICK</div>

  <section class="value accountability">
    <svg class="value-icon" viewBox="0 0 116 116" aria-hidden="true">
      <circle cx="58" cy="58" r="53" fill="#fff" stroke="#3aaa35" stroke-width="7"/>
      <rect x="44" y="34" width="30" height="38" rx="2" fill="#111"/>
      <path d="M49 44 H69 M49 51 H69 M49 58 H63" stroke="#fff" stroke-width="3"/>
      <circle cx="38" cy="44" r="10" fill="none" stroke="#111" stroke-width="4"/>
      <path d="M45 51 L52 58" stroke="#111" stroke-width="5" stroke-linecap="round"/>
      <circle cx="72" cy="68" r="7" fill="#111"/>
      <path d="M60 86 C 60 74 84 74 84 86 Z" fill="#111"/>
    </svg>
    <h2 class="value-name">ACCOUNTABILITY:</h2>
    <p class="value-text">We take ownership of our work and<br>actions, ensuring reliability and trust<br>in every solution we deliver.</p>
  </section>

  <section class="value teamwork">
    <svg class="value-icon" viewBox="0 0 116 116" aria-hidden="true">
      <circle cx="58" cy="58" r="53" fill="#fff" stroke="#3aaa35" stroke-width="7"/>
      <circle cx="44" cy="52" r="13" fill="#111"/>
      <circle cx="72" cy="64" r="13" fill="#111"/>
      <path d="M30 76 L48 62 L68 54 L86 40" stroke="#111" stroke-width="8" stroke-linecap="round"/>
    </svg>
    <h2 class="value-name">TEAMWORK:</h2>
    <p class="value-text">We collaborate across departments and<br>disciplines to provide the highest level<br>of service and innovation for our clients.</p>
  </section>

  <section class="value integrity">
    <svg class="value-icon" viewBox="0 0 116 116" aria-hidden="true">
      <circle cx="58" cy="58" r="53" fill="#fff" stroke="#3aaa35" stroke-width="7"/>
      <circle cx="58" cy="58" r="22" fill="none" stroke="#111" stroke-width="3" stroke-dasharray="20 8"/>
      <circle cx="58" cy="58" r="12" fill="#111"/>
      <circle cx="58" cy="58" r="4" fill="#fff"/>
      <circle cx="28" cy="36" r="5" fill="#111"/>
      <path d="M20 50 C 20 42 36 42 36 50 Z" fill="#111"/>
      <circle cx="88" cy="78" r="5" fill="#111"/>
      <path d="M80 92 C 80 84 96 84 96 92 Z" fill="#111"/>
    </svg>
    <h2 class="value-name">INTEGRITY:</h2>
    <p class="value-text">We operate with honesty, transpar-<br>ency, and ethical standards in all<br>aspects of our business.</p>
  </section>

  <section class="value growth">
    <svg class="value-icon" viewBox="0 0 116 116" aria-hidden="true">
      <circle cx="58" cy="58" r="53" fill="#fff" stroke="#3aaa35" stroke-width="7"/>
      <path d="M58 24 L72 40 H64 V80 H52 V40 H44 Z" fill="#111"/>
      <path d="M38 50 L46 60 H42 V80 H34 V60 H30 Z" fill="#111"/>
      <path d="M78 50 L86 60 H82 V80 H74 V60 H70 Z" fill="#111"/>
      <path d="M26 84 H90 L94 92 H22 Z" fill="#111"/>
    </svg>
    <h2 class="value-name">GROWTH:</h2>
    <p class="value-text">We are committed to continuous<br>improvement—of our people, our pro-<br>cesses, and our impact in the industry.</p>
  </section>

  <p class="website">www.brovickeng.com</p>
</main>
</body>
</html>
```